Business card design needed

I run a Beautician studio (for 7 years now)
I offer
- Velmo Body Sugaring
- Ruby Glaze
- Nails
- Facials
- Manicure
- Foot Treatment
It might not be necessary to list all those treatments?
Maybe the link to the Website is sufficient?
I leave that up to you ...
(more info on www.FernAndDewByLenka.com.au)
Velmo BodySugaring is our biggest success, It replaces waxing.
I would like to incorporate the logo into the Business Card.
We had many complaints regarding our old Business Cards as the Phone Number was to small.
On the backside, we would like a "your next Appointment" section.
Looking forward to you Design, cheers ... Lenka
Industry/Entity Type
Business
Contact Information for Business Card
Fern by Dew by Lenka
14 Korrin Sqr 3942 Berwick
www.FernAndDewByLenka.com.au
03 9481 2267

```html
<!DOCTYPE html>
<html lang="en">
<head>
<meta charset="utf-8">
<title>Fern &amp; Dew by Lenka – Business Card</title>
<link rel="stylesheet" href="https://fonts.googleapis.com/css2?family=Open+Sans:ital,wght@0,400;0,600;1,600;1,700&family=Ubuntu:wght@400&family=Tinos&display=swap">
<style>
  :root {
    --backdrop: #ebe7e2;
    --card: #ffffff;
    --ink: #3a3a3a;
    --ink-soft: #555555;
    --band: #3b3b3d;
    --band-rule: #b9b9b9;
    --rule: #8a8a8a;
    --mark: #f0a020;
    --mark-faint: rgba(240, 160, 32, 0.12);
    --text-faint: rgba(120, 120, 120, 0.18);
  }
  * { box-sizing: border-box; margin: 0; padding: 0; }
  html, body { width: 1200px; height: 788px; overflow: hidden; }
  body {
    background: var(--backdrop);
    font-family: "Open Sans", Arial, sans-serif;
    color: var(--ink);
    position: relative;
  }
  .card {
    position: absolute;
    width: 526px;
    height: 300px;
    background: var(--card);
    border-radius: 22px;
    overflow: hidden;
    box-shadow: 0 2px 6px rgba(0,0,0,0.15);
  }
  .abs { position: absolute; white-space: nowrap; }

  /* Front */
  .card--front { left: 340px; top: 74px; }
  .front__band { left: 0; top: 0; width: 61px; height: 300px; background: var(--band); }
  .front__band-rule { left: 63px; top: 0; width: 6px; height: 300px; background: var(--band-rule); }
  .studio-name { font-family: "Ubuntu", "Trebuchet MS", sans-serif; letter-spacing: 0.5px; color: var(--ink); }
  .front__title { left: 82px; top: 40px; font-size: 34px; }
  .contact { left: 82px; font-size: 15.5px; display: flex; align-items: center; gap: 6px; color: var(--ink); }
  .contact svg { width: 13px; height: 13px; fill: var(--ink); }

  .brand { display: flex; flex-direction: column; align-items: center; gap: 4px; }
  .brand__dot { width: 58px; height: 58px; border-radius: 50%; background: var(--mark); }
  .brand__name { font-family: "Open Sans", sans-serif; font-size: 13px; letter-spacing: 1.5px; color: var(--ink); text-align: center; line-height: 1.25; }

  /* Back 1 */
  .card--back-one { left: 53px; top: 444px; }
  .back-one__title { left: 0; width: 526px; top: 10px; text-align: center; font-size: 27px; }
  .back-one__rule { left: 0; top: 50px; width: 526px; height: 1px; background: var(--rule); }
  .faint-mark { left: 160px; top: 90px; width: 230px; height: 230px; border-radius: 50%; background: var(--mark-faint); }
  .faint-name { left: 130px; top: 190px; font-size: 52px; letter-spacing: 8px; color: var(--text-faint); }
  .heading { font-style: italic; font-weight: 700; color: var(--ink); }
  .offer__heading { left: 30px; top: 68px; font-size: 17px; }
  .offer__list { left: 30px; top: 97px; list-style: none; font-family: "Tinos", "Times New Roman", serif; font-size: 14.5px; line-height: 20px; color: var(--ink-soft); }
  .offer__list li::before { content: ""; display: inline-block; width: 4px; height: 4px; background: var(--ink-soft); margin: 0 8px 3px 0; }
  .back-one__divider { left: 207px; top: 72px; width: 2px; height: 140px; background: var(--rule); }
  .appt__heading { left: 244px; top: 69px; font-size: 17px; }
  .field { left: 244px; font-size: 16px; display: flex; align-items: flex-end; color: var(--ink); }
  .field__line { display: inline-block; border-bottom: 1px solid var(--ink); height: 1px; margin: 0 4px 4px 0; }
  .hours-small__heading { left: 0; width: 526px; text-align: center; top: 238px; font-size: 14px; font-style: italic; font-weight: 600; }
  .hours-small__times { left: 0; width: 526px; text-align: center; top: 261px; font-size: 12.5px; word-spacing: 1px; }
  .hours-small__times span + span { margin-left: 48px; }

  /* Back 2 */
  .card--back-two { left: 621px; top: 444px; }
  .back-two__heading { left: 33px; top: 26px; font-size: 20px; letter-spacing: 1px; font-weight: 600; }
  .back-two__hours { left: 30px; top: 59px; font-size: 17px; line-height: 24px; }
  .back-two__brand { left: 378px; top: 16px; }
  .back-two__rule { left: 30px; top: 116px; width: 466px; height: 1px; background: #c8c8c8; }
  .next-appt { left: 46px; top: 143px; font-size: 18px; display: flex; align-items: flex-end; }
  .date-row { left: 35px; top: 193px; font-size: 18px; display: flex; align-items: flex-end; gap: 5px; }
  .days { left: 60px; top: 248px; display: flex; gap: 10px; font-size: 17px; }
  .day { display: flex; align-items: center; gap: 10px; margin-right: 8px; }
  .day__box { width: 22px; height: 22px; border: 1.5px solid var(--ink); }
</style>
</head>
<body>

<section class="card card--front" aria-label="Card front">
  <div class="abs front__band"></div>
  <div class="abs front__band-rule"></div>
  <h1 class="abs studio-name front__title">FERN&amp;DEW BY LENKA</h1>
  <p class="abs contact" style="top:202px">
    <svg viewBox="0 0 16 16" aria-hidden="true"><path d="M1 5c0-2 3-3 7-3s7 1 7 3v2h-4V5.5H5V7H1z M3 8h10l1 6H2z"/></svg>
    03 9481 2267
  </p>
  <p class="abs contact" style="top:226px">
    <svg viewBox="0 0 16 16" aria-hidden="true"><path d="M8 1l7 7h-2v7h-3.5v-4.5h-3V15H3V8H1z"/></svg>
    14 Korrin Sqr, 3942 Berwick
  </p>
  <p class="abs contact" style="top:251px">
    <svg viewBox="0 0 16 16" aria-hidden="true"><circle cx="8" cy="8" r="7"/></svg>
    www.FernAndDewByLenka.com.au
  </p>
  <div class="abs brand" style="left:382px; top:172px">
    <span class="brand__dot"></span>
    <span class="brand__name">VELMO<br>BODY SUGARING</span>
  </div>
</section>

<section class="card card--back-one" aria-label="Card back, services and appointment">
  <div class="abs faint-mark"></div>
  <div class="abs faint-name">VELMO</div>
  <h2 class="abs studio-name back-one__title">FERN&amp;DEW BY LENKA</h2>
  <div class="abs back-one__rule"></div>

  <h3 class="abs heading offer__heading">I offer</h3>
  <ul class="abs offer__list">
    <li>Velmo Body Sugaring</li>
    <li>Ruby Glaze</li>
    <li>Nails</li>
    <li>Facials</li>
    <li>Manicure</li>
    <li>Foot Treatment</li>
  </ul>
  <div class="abs back-one__divider"></div>

  <h3 class="abs heading appt__heading">An Appointment</h3>
  <p class="abs field" style="top:110px">Name<span class="field__line" style="width:217px"></span></p>
  <p class="abs field" style="top:150px">Date<span class="field__line" style="width:224px"></span></p>
  <p class="abs field" style="top:190px">time<span class="field__line" style="width:160px"></span>am / pm</p>

  <p class="abs hours-small__heading">Hours of Operation</p>
  <p class="abs hours-small__times"><span>Mon. to Fri.&nbsp; 7.30am - 7.00pm</span><span>Sat. 7.30am - 12.00pm</span></p>
</section>

<section class="card card--back-two" aria-label="Card back, next appointment">
  <h3 class="abs heading back-two__heading">Hours of Operation</h3>
  <p class="abs back-two__hours">Monday to Friday -&nbsp; 7.30am - 7.00pm<br>Saturday - 7.30am - 12.00pm</p>
  <div class="abs brand back-two__brand">
    <span class="brand__dot" style="width:52px;height:52px"></span>
    <span class="brand__name" style="font-size:12px">VELMO<br>BODY SUGARING</span>
  </div>
  <div class="abs back-two__rule"></div>

  <p class="abs next-appt"><span class="field__line" style="width:260px"></span>has an appointment</p>
  <p class="abs date-row">Date :<span class="field__line" style="width:40px"></span>/
    <span class="field__line" style="width:40px"></span>/
    <span class="field__line" style="width:50px"></span>@
    <span class="field__line" style="width:40px"></span>:
    <span class="field__line" style="width:50px;margin-right:0"></span>am / pm</p>

  <div class="abs days">
    <span class="day"><span class="day__box"></span>Mon.</span>
    <span class="day"><span class="day__box"></span>Tue.</span>
    <span class="day"><span class="day__box"></span>Wed.</span>
    <span class="day"><span class="day__box"></span>Thu.</span>
    <span class="day"><span class="day__box"></span>Fri.</span>
  </div>
</section>

</body>
</html>
```